New Business Card Design for Manufacturing

We are an engineering/manufacturing company that offers Advanced machining/assembly/engineering services, as well as innovative products for the heavy duty engine cooling markets.

We are looking to get a new business card designed that is clean and modern looking, but still fits the wide range of technical/skilled work we do.

- We hope to use this design as the base for other design work in new Presentations, web, and print work.

Industry/Entity Type

Engineering

Contact Information for Business Card

Our preferred color of blue is (RGB) 22/71/159 but can vary slightly from that color. Our content will be our Logo and full company name (Vantrell Forge Works, Inc.), company address, name, job title, phone number with extension, cell number, fax number, website, and email address on the cards.
We'd like the full company name next to the logo, but we are open to other interpretations of that layout.
Preferably, we would like the back side to be clean with just our logo, and the front to contain all of the contact information.

Colors
2f74b4
0355a3
85abd2

Requirements
Must have
• - Logo, company name, needed content - We are open to interpretation beyond that.
• - Standard size business card.
• - Horizontal orientation.
• - Enough space for lengthy names / job titles (for example, a job title could read "Directory of Human Resources" or "V.P. of Governmental Affairs"). We need this to look clean, whether the title be short (CEO) or long (as described above).

```html
<!DOCTYPE html>
<html lang="en">
<head>
<meta charset="utf-8">
<title>Vantrell Forge Works, Inc. — Business Card</title>
<link rel="stylesheet" href="https://fonts.googleapis.com/css2?family=Open+Sans:wght@400;600&display=swap">
<style>
  :root {
    --backdrop: #3a3a3c;
    --card: #232325;
    --card-edge: #1b1b1d;
    --brand-blue: #0f6cc0;
    --brand-blue-deep: #0355a3;
    --brand-blue-light: #2f74b4;
    --brand-blue-bright: #1a86d8;
    --text-light: #f2f2f2;
    --emboss: #3a3a3e;
  }
  * { box-sizing: border-box; margin: 0; padding: 0; }
  html, body { width: 799px; height: 1200px; overflow: hidden; }
  body {
    background: var(--backdrop);
    font-family: "Open Sans", Arial, sans-serif;
    position: relative;
  }
  .card {
    position: absolute;
    left: 90px;
    width: 620px;
    height: 354px;
    background: var(--card);
    border: 1px solid var(--card-edge);
    box-shadow: 0 18px 40px rgba(0,0,0,0.45);
    overflow: hidden;
  }
  .card--back { top: 140px; }
  .card--front { top: 700px; }

  .back-name {
    position: absolute;
    inset: 0;
    display: flex;
    align-items: center;
    justify-content: center;
    font-size: 34px;
    font-weight: 600;
    color: var(--emboss);
    letter-spacing: 0.5px;
  }

  .front-accent {
    position: absolute;
    left: 360px;
    top: 0;
    right: 0;
    height: 220px;
    background: linear-gradient(135deg, var(--brand-blue-bright), var(--brand-blue-deep));
  }

  .front-brand {
    position: absolute;
    left: 40px;
    top: 118px;
    display: flex;
    align-items: center;
    gap: 10px;
    font-size: 21px;
    font-weight: 600;
    color: var(--brand-blue-light);
  }
  .front-brand__mark {
    width: 14px; height: 14px;
    background: var(--brand-blue-light);
  }

  .person {
    position: absolute;
    right: 30px;
    top: 118px;
    text-align: right;
    color: var(--text-light);
  }
  .person__name { font-size: 24px; font-weight: 600; }
  .person__title { font-size: 14px; font-weight: 400; margin-top: 2px; }

  .address {
    position: absolute;
    left: 40px;
    top: 196px;
    font-size: 14px;
    font-style: normal;
    line-height: 1.45;
    color: var(--text-light);
  }
  .address__web { color: var(--brand-blue-light); }

  .contacts {
    position: absolute;
    right: 28px;
    bottom: 26px;
    list-style: none;
    font-size: 14px;
    line-height: 1.5;
    color: var(--text-light);
  }
  .contacts__item {
    display: flex;
    justify-content: flex-end;
    align-items: center;
    gap: 9px;
  }
  .contacts__icon { width: 13px; height: 13px; fill: var(--brand-blue-light); flex: none; }
</style>
</head>
<body>

<section class="card card--back" aria-label="Card back">
  <div class="back-name">Vantrell Forge Works, Inc.</div>
</section>

<section class="card card--front" aria-label="Card front">
  <div class="front-accent" role="img" aria-label="Decorative blue and grey swoosh area"></div>

  <div class="front-brand">
    <span class="front-brand__mark"></span>
    <span>Vantrell Forge Works, Inc.</span>
  </div>

  <div class="person">
    <div class="person__name">Marcus Lee Harlan</div>
    <div class="person__title">Managing Director</div>
  </div>

  <address class="address">
    <div>58 Foundry Row, Millbrook,</div>
    <div>Carver Falls, US 40218</div>
    <div class="address__web">www.vantrellforge.com</div>
  </address>

  <ul class="contacts">
    <li class="contacts__item">555-0142-2140 (Ext. 214)
      <svg class="contacts__icon" viewBox="0 0 16 16"><path d="M3 1h3l1.5 4-2 1.3a9 9 0 0 0 4.2 4.2L11 8.5l4 1.5v3a2 2 0 0 1-2 2A13 13 0 0 1 1 3a2 2 0 0 1 2-2z"/></svg>
    </li>
    <li class="contacts__item">555-0187-3392
      <svg class="contacts__icon" viewBox="0 0 16 16"><path d="M4.5 0h7a1.5 1.5 0 0 1 1.5 1.5v13A1.5 1.5 0 0 1 11.5 16h-7A1.5 1.5 0 0 1 3 14.5v-13A1.5 1.5 0 0 1 4.5 0zM5 2v10h6V2zm3 11a1 1 0 1 0 0 2 1 1 0 0 0 0-2z"/></svg>
    </li>
    <li class="contacts__item">555-0163-4471
      <svg class="contacts__icon" viewBox="0 0 16 16"><path d="M4 0h7l2 2v4H4zM1 7h14v7H12v2H4v-2H1zm4 5v3h6v-3z"/></svg>
    </li>
    <li class="contacts__item">mharlan@vantrellforge.com
      <svg class="contacts__icon" viewBox="0 0 16 16"><path d="M0 3h16v1.2L8 9 0 4.2zm0 2.6 8 4.8 8-4.8V13H0z"/></svg>
    </li>
  </ul>
</section>

</body>
</html>
```